PWNF Traditional Business Card Project

Please see attached....just a simple business card... on attachment- please use the exact font, style, etc as the attached "Ned Farley Broughton" card... however, replace with the "Walter Augustin Pryde" text and address below the card.

```html
<!DOCTYPE html>
<html lang="en">
<head>
<meta charset="utf-8">
<title>PWNF Business Card</title>
<link rel="stylesheet" href="https://fonts.googleapis.com/css2?family=Old+Standard+TT:wght@700&family=Arimo:wght@400&display=swap">
<style>
  :root {
    --page-bg: #ecebe8;
    --card-frame: #9d9d9d;
    --card-face: #dcdedd;
    --corner: #ffffff;
    --ink: #161616;
    --ink-soft: #2a2a2a;
  }
  * { margin: 0; padding: 0; box-sizing: border-box; }
  html, body { width: 1200px; height: 902px; overflow: hidden; }
  body {
    background: var(--page-bg);
    display: flex; align-items: center; justify-content: center;
  }
  .business-card {
    position: relative;
    width: 1000px; height: 572px;
    background: var(--card-frame);
    padding: 22px;
  }
  .card-face {
    position: relative;
    width: 100%; height: 100%;
    background: var(--card-face);
    color: var(--ink);
  }
  .corner {
    position: absolute; width: 70px; height: 44px;
    border-color: var(--corner); border-style: solid; border-width: 0;
  }
  .corner--tl { top: 0; left: 0; border-top-width: 9px; border-left-width: 9px; }
  .corner--tr { top: 0; right: 0; border-top-width: 9px; border-right-width: 9px; }
  .corner--bl { bottom: 0; left: 0; border-bottom-width: 9px; border-left-width: 9px; }
  .corner--br { bottom: 0; right: 0; border-bottom-width: 9px; border-right-width: 9px; }

  .serif-caps {
    font-family: "Old Standard TT", "Times New Roman", serif;
    font-weight: 700;
    font-variant: small-caps;
    letter-spacing: 0.02em;
  }
  .sans {
    font-family: "Arimo", Arial, sans-serif;
  }

  .firm { position: absolute; top: 30px; left: 40px; }
  .firm__name { font-size: 40px; line-height: 1; }
  .firm__suffix {
    margin-top: 8px; font-size: 15px; letter-spacing: 0.2em;
    text-transform: uppercase; color: var(--ink-soft);
  }

  .attorney { position: absolute; top: 200px; left: 0; right: 0; text-align: center; }
  .attorney__name { font-size: 54px; line-height: 1; }
  .attorney__title {
    margin-top: 10px; padding-left: 170px;
    font-size: 18px; letter-spacing: 0.42em; text-transform: uppercase;
    color: var(--ink-soft);
  }

  .contact-lines { position: absolute; font-size: 24px; line-height: 1.3; }
  .address { left: 40px; bottom: 36px; text-transform: none; }
  .address .upper { text-transform: uppercase; letter-spacing: 0.06em; }
  .direct { right: 40px; top: 330px; text-align: right; }
  .direct .upper { text-transform: uppercase; letter-spacing: 0.04em; }
</style>
</head>
<body>
  <article class="business-card">
    <div class="card-face">
      <span class="corner corner--tl"></span>
      <span class="corner corner--tr"></span>
      <span class="corner corner--bl"></span>
      <span class="corner corner--br"></span>

      <header class="firm">
        <div class="firm__name serif-caps">Pacific Westview</div>
        <div class="firm__suffix sans">Northfield Group, PLC</div>
      </header>

      <section class="attorney">
        <h1 class="attorney__name serif-caps">Walter Augustin Pryde</h1>
        <p class="attorney__title sans">Attorney at Law</p>
      </section>

      <address class="contact-lines address sans">
        <div class="upper">2470 Cedar Avenue, Suite B</div>
        <div class="upper">Alder Springs, CA 95013</div>
        <div>www.pwnflaw.com</div>
      </address>

      <div class="contact-lines direct sans">
        <div class="upper">Tel (555) 214-3300</div>
        <div class="upper">Fax (555) 214-3301</div>
        <div>wpryde@pwnflaw.com</div>
      </div>
    </div>
  </article>
</body>
</html>
```